Build PowerPoint for New Logo & Letterhead

I have started my own consulting firm and created a logo and letterhead (attached) am looking PowerPoint template. My name is Dorrit Vandermolen and the company is called K Quadrant Advisory. We primarily use PowerPoint files to display analyses, maps and key talking points from interviews and/or recommendations. We use the documents more to facilitate discussion with our target audiences. Most of the time our PowerPoint document is printed as handouts for our clients and not projected.

Target Market(s)

Healthcare provider organizations (hospitals, health systems, physician groups)

Industry/Entity Type

Healthcare

Font styles to use
Sans Serif

Colors
abd036
1f9ad1
0355a3

Requirements
Must have
• I would like to cover page to play off of the letterhead in some fashion. I want the design to provide plenty of space for text, graphics, maps, pictures, etc.
• We will usually include our clients logo somewhere on the document. Historically it is prominent on the cover page and then in one of the corners on all of the pages thereafter.

```html
<!DOCTYPE html>
<html lang="en">
<head>
<meta charset="utf-8">
<title>K Quadrant Advisory — Presentation Cover</title>
<link rel="stylesheet" href="https://fonts.googleapis.com/css2?family=PT+Sans:wght@400;700&family=Inter:wght@300&display=swap">
<style>
  :root {
    --backdrop: #d5d6d8;
    --brand-navy: #0355a3;
    --brand-blue: #1f9ad1;
    --brand-green: #abd036;
    --deep-blue: #0062a3;
    --glow-blue: #42a9d9;
    --white: #ffffff;
    --ink-grey: #555a60;
  }
  html, body {
    margin: 0;
    padding: 0;
    width: 1200px;
    height: 900px;
    overflow: hidden;
    background: var(--backdrop);
  }
  .cover-slide {
    position: absolute;
    left: 234px;
    top: 222px;
    width: 720px;
    height: 405px;
    background: var(--white);
    overflow: hidden;
  }
  .hero-band {
    position: absolute;
    left: 0;
    top: 0;
    width: 720px;
    height: 312px;
  }
  .title-block {
    position: absolute;
    right: 60px;
    top: 108px;
    text-align: right;
    color: var(--white);
  }
  .title-main {
    margin: 0;
    font-family: "PT Sans", sans-serif;
    font-weight: 700;
    font-size: 37px;
    line-height: 1;
    letter-spacing: -0.5px;
  }
  .title-sub {
    margin: 8px 0 0;
    font-family: "Inter", sans-serif;
    font-weight: 300;
    font-size: 18px;
    letter-spacing: 3.3px;
    margin-right: -3px;
  }
  .title-meta {
    margin: 12px 0 0;
    font-family: "PT Sans", sans-serif;
    font-size: 13px;
  }
  .client-name {
    position: absolute;
    left: 424px;
    top: 326px;
    display: flex;
    align-items: center;
    gap: 6px;
    font-family: "PT Sans", sans-serif;
    font-weight: 700;
    font-size: 17px;
    color: var(--brand-blue);
  }
  .client-name .mark {
    width: 14px;
    height: 14px;
    background: var(--brand-blue);
  }
  .firm-name {
    position: absolute;
    left: 568px;
    top: 300px;
    width: 130px;
    display: flex;
    align-items: center;
    gap: 8px;
    font-family: "PT Sans", sans-serif;
    font-weight: 700;
    font-size: 17px;
    line-height: 1.1;
    color: var(--brand-navy);
  }
  .firm-name .mark {
    flex: none;
    width: 22px;
    height: 22px;
    background: var(--brand-green);
  }
  .footer-rule {
    position: absolute;
    left: 0;
    bottom: 0;
    width: 720px;
    height: 9px;
    background: var(--brand-green);
  }
</style>
</head>
<body>
  <section class="cover-slide">
    <svg class="hero-band" viewBox="0 0 720 312" aria-hidden="true">
      <defs>
        <radialGradient id="heroGlow" cx="374" cy="170" r="330" gradientUnits="userSpaceOnUse">
          <stop offset="0" stop-color="var(--glow-blue)"/>
          <stop offset="0.55" stop-color="#1479b9"/>
          <stop offset="1" stop-color="var(--deep-blue)"/>
        </radialGradient>
      </defs>
      <path d="M0 0 H720 V272 H458 C425 272 410 280 395 294 C382 306 370 312 348 312 H0 Z" fill="url(#heroGlow)"/>
    </svg>

    <div class="title-block">
      <h1 class="title-main">WELCOME</h1>
      <p class="title-sub">TO OUR PRESENTATION</p>
      <p class="title-meta">Birmingham, March 25, 2011</p>
    </div>

    <div class="client-name"><span class="mark"></span>Halvern Health</div>
    <div class="firm-name"><span class="mark"></span>K Quadrant Advisory</div>

    <div class="footer-rule"></div>
  </section>
</body>
</html>
```